Professional and creative business card design for recruiting service providers

Our company supports German medium-sized companies in filling vacancies promptly. For this we use social media marketing and bring our customers into the visibility.

We want a professional but also creative design for our business cards.

Please look at lindqvar-staff.de to get an impression of our CI.

Target Market(s)

Small and medium-sized companies in Germany from the industry

Industry/Entity Type

Industrie, Handwerk

Contact Information for Business Card

Name, Position, Telefonnummer, Email, Website

Colors
EE7325
F08F49
F5BC92
FAE3D3
FDF4ED

Requirements
Must have
• A picture of the employee and in the style of www.lindqvar-staff.de

```html
<!DOCTYPE html>
<html lang="de">
<head>
<meta charset="utf-8">
<title>Lindqvar Staff – Visitenkarte</title>
<link rel="stylesheet" href="https://fonts.googleapis.com/css2?family=Poppins:wght@400;500;600;700&display=swap">
<style>
  :root {
    --orange: #ee5a24;
    --orange-light: #f08f49;
    --orange-deep: #c8411a;
    --ink: #161616;
    --rule: #7a7a7a;
    --paper: #ffffff;
    --backdrop: #1d1d1f;
    --photo-light: #e6e6e8;
    --photo-mid: #c9c9cd;
  }
  * { box-sizing: border-box; margin: 0; padding: 0; }
  html, body {
    width: 1200px; height: 1108px; overflow: hidden;
    background: var(--backdrop);
    font-family: "Poppins", sans-serif;
  }
  .canvas {
    position: relative; width: 1200px; height: 1108px;
    display: flex; justify-content: center; align-items: center; gap: 70px;
  }
  .card {
    width: 420px; height: 680px; border-radius: 22px; overflow: hidden;
    position: relative;
  }
  .card--front { background: var(--paper); display: flex; flex-direction: column; }
  .portrait {
    height: 300px;
    background: linear-gradient(180deg, var(--photo-light) 0%, var(--photo-mid) 55%, #3a3a40 100%);
  }
  .details { flex: 1; display: flex; flex-direction: column; align-items: center; padding: 26px 40px 0; }
  .person-name {
    color: var(--orange); font-weight: 600; font-size: 30px; letter-spacing: 1px;
    text-transform: uppercase; line-height: 1.1;
  }
  .person-role { color: var(--ink); font-size: 17px; margin-top: 2px; }
  .icon-rule { display: flex; align-items: center; width: 100%; gap: 8px; margin-top: 16px; }
  .icon-rule .line { flex: 1; height: 1px; background: var(--rule); }
  .icon-box {
    width: 32px; height: 32px; border-radius: 5px; background: var(--orange);
    display: flex; align-items: center; justify-content: center;
  }
  .contact-list { list-style: none; text-align: center; margin-top: 14px; color: var(--ink); font-size: 19px; line-height: 1.45; letter-spacing: .3px; }
  .rule { width: 100%; height: 1px; background: var(--ink); margin-top: 16px; opacity: .7; }
  .brand { display: flex; align-items: center; gap: 18px; margin-top: 30px; }
  .brand-square { width: 58px; height: 58px; background: var(--orange); }
  .brand-name { font-weight: 700; font-size: 30px; line-height: 1.05; color: var(--ink); letter-spacing: 2px; text-transform: uppercase; }
  .card--back {
    background: linear-gradient(200deg, var(--orange-light) 0%, var(--orange) 45%, var(--orange-deep) 100%);
  }
  .back-name {
    position: absolute; left: 0; right: 0; top: 440px; text-align: center;
    color: var(--paper); font-weight: 700; font-size: 22px; letter-spacing: 3px; text-transform: uppercase;
  }
</style>
</head>
<body>
<main class="canvas">
  <article class="card card--front">
    <div class="portrait" role="img" aria-label="Portraitfoto des Mitarbeiters im Büro"></div>
    <section class="details">
      <h1 class="person-name">Jonas Berger</h1>
      <p class="person-role">Managing Director</p>
      <div class="icon-rule">
        <span class="line"></span>
        <span class="icon-box">
          <svg width="18" height="18" viewBox="0 0 24 24" fill="#fff" aria-label="Telefon"><path d="M6.6 10.8a15 15 0 0 0 6.6 6.6l2.2-2.2a1 1 0 0 1 1-.25 11.4 11.4 0 0 0 3.6.57 1 1 0 0 1 1 1V20a1 1 0 0 1-1 1A17 17 0 0 1 3 4a1 1 0 0 1 1-1h3.5a1 1 0 0 1 1 1c0 1.25.2 2.45.57 3.6a1 1 0 0 1-.25 1z"/></svg>
        </span>
        <span class="icon-box">
          <svg width="18" height="18" viewBox="0 0 24 24" fill="none" stroke="#fff" stroke-width="2" aria-label="E-Mail"><rect x="3" y="5" width="18" height="14" rx="1"/><path d="M3 6l9 7 9-7"/></svg>
        </span>
        <span class="icon-box">
          <svg width="18" height="18" viewBox="0 0 24 24" fill="none" stroke="#fff" stroke-width="2" aria-label="Website"><circle cx="12" cy="12" r="9"/><path d="M3 12h18M12 3c3 3 3 15 0 18M12 3c-3 3-3 15 0 18"/></svg>
        </span>
        <span class="line"></span>
      </div>
      <ul class="contact-list">
        <li>040-987 654 321</li>
        <li>info@lindqvar-staff.de</li>
        <li>www.lindqvar-staff.de</li>
      </ul>
      <div class="rule"></div>
      <div class="brand">
        <span class="brand-square"></span>
        <span class="brand-name">Lindqvar<br>Staff</span>
      </div>
    </section>
  </article>

  <article class="card card--back" role="img" aria-label="Orange Rückseite mit dezentem Markenmuster">
    <p class="back-name">Lindqvar Staff</p>
  </article>
</main>
</body>
</html>
```